Business Card Design

We are a company that provides stump grinding services for residential and commercial clients. Looking for a simple business card design that may have some type of graphic on the card that will tie in with the Tamsen name(Grizzly Bear, Paw Print, etc) . Possibly some foliage wrapping around part of the card? Would like to have a simple design that stands out because it is unique. We are working on getting the website set up and there is a simple graphic on the top of the page that came to mind when I mentioned the leaves.

Industry/Entity Type

Business

Contact Information for Business Card

Tamsen Stump Grinding 303-257-4788KodiakStumps.Com

Font styles to use
Serif

Requirements
Must have
• Business name
• Website Address
• Phone Number
Nice to have
• Graphics that would be associated with a Tamsen bear.
Should not have
• Nothing frilly

```html
<!DOCTYPE html>
<html lang="en">
<head>
<meta charset="utf-8">
<title>Tamsen Stump Grinding – Business Card</title>
<link rel="stylesheet" href="https://fonts.googleapis.com/css2?family=Playfair+Display:wght@600&family=Open+Sans:wght@400&display=swap">
<style>
  :root {
    --backdrop: #3b3c3f;
    --ink: #0b0b0b;
    --paper: #ffffff;
    --card-shadow: rgba(0, 0, 0, 0.45);
  }
  html, body {
    margin: 0;
    padding: 0;
    width: 1200px;
    height: 864px;
    overflow: hidden;
    background: var(--backdrop);
  }
  .canvas {
    position: relative;
    width: 1200px;
    height: 864px;
    display: flex;
    flex-direction: column;
    align-items: center;
    justify-content: center;
    gap: 56px;
  }
  .card {
    width: 600px;
    height: 343px;
    box-sizing: border-box;
    position: relative;
    display: flex;
    flex-direction: column;
    align-items: center;
    box-shadow: 0 8px 24px var(--card-shadow);
  }
  .card--front {
    background: var(--ink);
    color: var(--paper);
    justify-content: center;
  }
  .card--back {
    background: var(--paper);
    color: var(--ink);
    justify-content: flex-start;
    padding-top: 70px;
  }
  .business-name {
    margin: 0;
    font-family: "Playfair Display", Georgia, serif;
    font-weight: 600;
    font-size: 40px;
    letter-spacing: 0.5px;
    white-space: nowrap;
  }
  .contact {
    margin-top: auto;
    margin-bottom: 56px;
    font-family: "Open Sans", Arial, sans-serif;
    font-size: 14px;
    line-height: 22px;
    display: flex;
    flex-direction: column;
    align-items: center;
  }
  .contact-line {
    display: flex;
    align-items: center;
    gap: 6px;
  }
  .contact-icon {
    width: 11px;
    height: 11px;
    fill: none;
    stroke: var(--ink);
    stroke-width: 1.6;
  }
  .contact-icon--solid {
    fill: var(--ink);
    stroke: none;
  }
</style>
</head>
<body>
<main class="canvas">
  <section class="card card--front">
    <h1 class="business-name">Tamsen Stump Grinding</h1>
  </section>

  <section class="card card--back">
    <h2 class="business-name">Tamsen Stump Grinding</h2>
    <div class="contact">
      <div class="contact-line">
        <svg class="contact-icon contact-icon--solid" viewBox="0 0 12 12" aria-hidden="true">
          <path d="M1 4 Q6 0 11 4 L9.5 5.5 L8 4.5 L8 3.6 Q6 3 4 3.6 L4 4.5 L2.5 5.5 Z"/>
          <rect x="2.5" y="6" width="7" height="5" rx="1"/>
        </svg>
        <span class="contact-phone">303-555-0146</span>
      </div>
      <div class="contact-line">
        <svg class="contact-icon" viewBox="0 0 12 12" aria-hidden="true">
          <rect x="1" y="5.5" width="6" height="3.5" rx="1.75" transform="rotate(-45 4 7.25)"/>
          <rect x="5" y="3" width="6" height="3.5" rx="1.75" transform="rotate(-45 8 4.75)"/>
        </svg>
        <span class="contact-web">TamsenStumps.Com</span>
      </div>
    </div>
  </section>
</main>
</body>
</html>
```